Business Card: RW Office Partners - Your organised problem solver

Business Name: RW Office Partners
Website: www.rwofficepartners.com.au
Email: marisol@rwofficepartners.com.au
Mobile: 61 482 907 236
Facebook: @rwofficepartners
Instrgram: @rwofficepartners

Brading Colours:
HEX
#986474
#ddccd3
#7a8498
#c9d8e4
#000000
#ffffff

Tag Line: Your dependable task finisher

Link to DRAFT website:
https://deskhelpcollective.wixsite.com/rw-office-partners

About Page from the website:
My name is Marisol Wrenfield, and I would love to assist you to become more productive in your day to day and achieve your business and personal goals.
My mission is to give you time, time to work on the important tasks of your business or to be able to spend more time with your family. I will take on the tasks you don’t have time for, don’t know well or simply don’t like to do.
I have an extensive background in Administration, Tender Coordination, Document Control, WHS and Quality Management working primarily in the Construction, Mining and Corporate World.
I am passionate about being organised, having order and making things in your life (and mine) easier! I love to watch something unfold and grow into something amazing! I am known for being the go-to problem solver, the organiser of all things, producing high standards of work even under pressure. I’m also a confident communicator, and I understand that you’re busy running your business.

Target Market(s)

Small to Medium Business who require assistance in their business by a virtual assistant.

Industry/Entity Type

Virtual Assistant

Contact Information for Business Card

Mobile: 61 482 907 236

Font styles to use
Sans Serif

Colors
ffffff

Requirements
Must have
• Branding Colours as outlined.
Contact Details as outlined.
Logo as provided.
Proper contact details - mobile, facebook, instragm, website.
Simple, Elegant, very clean looking.
Should not have
• Note cute with pictures.
Not too girly as still want to market to construction companies.

```html
<!DOCTYPE html>
<html lang="en">
<head>
<meta charset="utf-8">
<title>RW Office Partners – Business Card</title>
<link href="https://fonts.googleapis.com/css2?family=Montserrat:wght@500;600;700&family=Arimo:wght@400&display=swap" rel="stylesheet">
<style>
  :root {
    --mauve: #986474;
    --mauve-light: #ddccd3;
    --slate: #7a8498;
    --slate-light: #c9d8e4;
    --card: #0b0b0c;
    --card-edge: #151517;
    --backdrop: #2b2b2c;
    --white: #ffffff;
    --rule: #6c6c70;
  }
  * { box-sizing: border-box; margin: 0; padding: 0; }
  html, body { width: 1200px; height: 900px; overflow: hidden; }
  body {
    background: var(--backdrop);
    font-family: "Montserrat", sans-serif;
    position: relative;
  }
  .card {
    position: absolute;
    left: 340px;
    width: 520px;
    height: 300px;
    background: linear-gradient(160deg, var(--card-edge), var(--card) 60%);
    overflow: hidden;
  }
  .card--front { top: 120px; }
  .card--back { top: 470px; }

  .accent-band {
    position: absolute;
    left: 0; right: 0; bottom: 0;
    height: 8px;
    display: flex;
  }
  .accent-band__mauve { flex: 0 0 52%; background: var(--mauve); }
  .accent-band__slate { flex: 1; background: var(--slate); }

  /* front */
  .brand {
    position: absolute;
    top: 100px; left: 0; right: 0;
    display: flex;
    flex-direction: column;
    align-items: center;
  }
  .brand__mark {
    display: flex;
    align-items: center;
    gap: 14px;
  }
  .brand__square {
    width: 30px; height: 30px;
    background: var(--mauve);
  }
  .brand__name {
    font-weight: 600;
    font-size: 34px;
    color: var(--mauve);
    letter-spacing: 0.5px;
  }
  .brand__tagline {
    margin-top: 14px;
    font-weight: 700;
    font-size: 14.5px;
    color: var(--white);
    letter-spacing: 0.3px;
    text-transform: uppercase;
  }

  /* back */
  .contact {
    position: absolute;
    top: 48px; left: 0; right: 0;
    display: flex;
    flex-direction: column;
    align-items: center;
  }
  .contact__name {
    font-weight: 700;
    font-size: 17px;
    color: var(--mauve);
    text-transform: uppercase;
    letter-spacing: 0.5px;
  }
  .divider {
    display: flex;
    align-items: center;
    gap: 6px;
    margin: 10px 0 8px;
  }
  .divider__line { width: 48px; height: 1px; background: var(--rule); }
  .icon-tile {
    width: 20px; height: 20px;
    border-radius: 3px;
    background: var(--mauve);
    display: flex; align-items: center; justify-content: center;
  }
  .social-dot {
    width: 24px; height: 24px;
    border-radius: 50%;
    border: 1px solid var(--slate);
  }
  .contact__line {
    font-family: "Arimo", sans-serif;
    font-size: 15px;
    line-height: 19px;
    color: var(--white);
  }
</style>
</head>
<body>

  <section class="card card--front">
    <div class="brand">
      <div class="brand__mark">
        <span class="brand__square"></span>
        <span class="brand__name">RW Office Partners</span>
      </div>
      <p class="brand__tagline">Your dependable task finisher</p>
    </div>
    <div class="accent-band"><span class="accent-band__mauve"></span><span class="accent-band__slate"></span></div>
  </section>

  <section class="card card--back">
    <div class="contact">
      <h1 class="contact__name">Marisol Wrenfield</h1>
      <div class="divider">
        <span class="divider__line"></span>
        <span class="icon-tile" aria-label="Phone">
          <svg width="13" height="13" viewBox="0 0 24 24"><path fill="#0b0b0c" d="M6.6 10.8a15 15 0 0 0 6.6 6.6l2.2-2.2c.3-.3.7-.4 1-.2 1.1.4 2.3.6 3.6.6.6 0 1 .4 1 1V20c0 .6-.4 1-1 1A17 17 0 0 1 3 4c0-.6.4-1 1-1h3.5c.6 0 1 .4 1 1 0 1.3.2 2.5.6 3.6.1.3 0 .7-.2 1z"/></svg>
        </span>
        <span class="icon-tile" aria-label="Email">
          <svg width="13" height="13" viewBox="0 0 24 24"><rect x="2" y="5" width="20" height="14" fill="#0b0b0c"/><path d="M2 5l10 8 10-8" stroke="#986474" stroke-width="2" fill="none"/></svg>
        </span>
        <span class="icon-tile" aria-label="Website">
          <svg width="13" height="13" viewBox="0 0 24 24"><circle cx="12" cy="12" r="9" fill="none" stroke="#0b0b0c" stroke-width="2.2"/><path d="M3 12h18M12 3c3 3 3 15 0 18M12 3c-3 3-3 15 0 18" stroke="#0b0b0c" stroke-width="1.6" fill="none"/></svg>
        </span>
        <span class="divider__line"></span>
      </div>
      <p class="contact__line">61 482 907 236</p>
      <p class="contact__line">marisol@rwofficepartners.com.au</p>
      <p class="contact__line">www.rwofficepartners.com.au</p>
      <div class="divider">
        <span class="divider__line"></span>
        <span class="social-dot" aria-label="Social profile"></span>
        <span class="social-dot" aria-label="Social profile"></span>
        <span class="divider__line"></span>
      </div>
      <p class="contact__line">@rwofficepartners</p>
    </div>
    <div class="accent-band"><span class="accent-band__mauve"></span><span class="accent-band__slate"></span></div>
  </section>

</body>
</html>
```